New web design for a service provider in the medical field

We are looking for a new design for our website. We are a company that repairs and sells medical endoscopes. Our customers include doctors and hospitals. Our current website can be found at https://lumavex.de/en/lumavex-english.
We need a new web design (without programming) for the following 3 pages:
-Startpage https://lumavex.de/en/lumavex-english/
-Used endoscopes https://lumavex.de/en/used-endoscopes/
-Purchase https://lumavex.de/en/purchase/
The design should be modern and stylish.
The blue color of the logo should be reflected on the page, but not too intrusive.
I have uploaded the images from the header. If more images are needed, let me know and I will upload them.

Target Market(s)
Doctors and hospitals

```html
<!DOCTYPE html>
<html lang="en">
<head>
<meta charset="utf-8">
<title>Lumavex – Endoscope Repair &amp; Sale</title>
<link rel="stylesheet" href="https://fonts.googleapis.com/css2?family=Montserrat:wght@400;500;600;700;800&family=Quicksand:wght@400;500;600;700&display=swap">
<style>
:root{
  --blue:#2a9fd8;
  --blue-dark:#1f86bd;
  --ink:#1b2f3d;
  --text:#4a5864;
  --navy:#263f52;
  --navy-deep:#223847;
  --pale:#eaf3f9;
  --line:#c9d3da;
  --white:#fff;
}
*{box-sizing:border-box;margin:0;padding:0}
html,body{width:1200px;height:4854px;overflow:hidden}
body{font-family:"Quicksand",sans-serif;color:var(--text);background:var(--white);position:relative}
.abs{position:absolute}
h1,h2,h3,h4,.head{font-family:"Montserrat",sans-serif;color:var(--ink)}
.btn{position:absolute;display:flex;align-items:center;justify-content:center;font-family:"Montserrat",sans-serif;font-weight:600;font-size:14px;letter-spacing:.3px;text-transform:uppercase}
.brand{font-family:"Montserrat",sans-serif;font-weight:700;color:var(--ink);display:flex;align-items:center;gap:10px}
.brand .dot{width:14px;height:14px;border-radius:50%;background:var(--blue)}

/* header */
.topbar{left:678px;top:0;width:522px;height:40px;background:var(--blue);clip-path:polygon(4% 0,100% 0,100% 100%,0 100%);color:#fff;font-family:"Montserrat",sans-serif;font-size:12px;font-weight:600;display:flex;align-items:center;gap:24px;padding-left:44px}
.topbar span{display:flex;align-items:center;gap:6px}
.header-brand{left:96px;top:38px;font-size:28px}
.nav{left:298px;top:76px;display:flex;gap:34px;font-family:"Montserrat",sans-serif;font-size:12px;font-weight:700;color:var(--ink)}
.nav .active{border-bottom:2px solid var(--ink);padding-bottom:8px}

/* hero */
.hero{left:0;top:117px;width:1200px;height:576px;background:linear-gradient(100deg,#e9f0f6 0%,#dfe8f0 45%,#cfd8e0 70%,#e4eaef 100%)}
.hero-eyebrow{left:100px;top:296px;font-size:17px;letter-spacing:3px;color:var(--blue);font-weight:500}
.hero-title{left:100px;top:322px;font-size:38px;font-weight:800;line-height:46px;color:var(--navy)}
.hero-btn{left:107px;top:443px;width:178px;height:52px;border:2px solid var(--navy);color:var(--blue);border-radius:3px;font-weight:500;font-size:16px}

/* intro */
.section-title{position:absolute;left:0;width:1200px;text-align:center;font-size:33px;font-weight:800;color:var(--navy)}
.rule{position:absolute;width:60px;height:3px;background:var(--blue)}
.intro-text{left:230px;top:836px;width:740px;text-align:center;font-size:19px;line-height:32px;color:var(--ink)}

/* about */
.about-accent{left:122px;top:1110px;width:282px;height:284px;background:var(--blue)}
.about-photo{left:136px;top:1036px;width:450px;height:345px;background:linear-gradient(120deg,#f1f3f5,#9aa2a8 50%,#e4e7ea)}
.about-bar{left:642px;top:1050px;width:3px;height:86px;background:var(--blue)}
.about-title{left:657px;top:1050px;width:490px;font-size:22px;line-height:29px;font-weight:800;color:var(--navy)}
.about-text{left:642px;top:1158px;width:500px;font-size:15.5px;line-height:25px;color:var(--ink)}
.about-text p+p{margin-top:12px}

/* offer cards */
.offer{position:absolute;top:1558px;width:307px;height:311px;border:2px solid var(--line);text-align:center}
.offer-icon{position:absolute;top:-47px;left:103px;width:98px;height:92px;display:flex;align-items:center;justify-content:center;border:4px solid #fff;outline:2px solid var(--line)}
.offer h3{margin-top:68px;font-size:19px;font-weight:700;color:var(--navy)}
.offer .sub{font-size:14px;color:var(--ink);margin-top:4px;font-weight:500}
.offer p.desc{font-size:11.5px;line-height:19px;margin:16px 30px 0;color:var(--text)}
.offer .btn{left:50px;bottom:28px;width:205px;height:44px;border:2px solid var(--blue);color:var(--navy);font-size:13px}

/* faulty band */
.faulty{left:0;top:1956px;width:620px;height:516px;background:linear-gradient(135deg,#2f9dd5,#2a8ec8)}
.faulty-photo{left:620px;top:1956px;width:580px;height:516px;background:linear-gradient(160deg,#f4f6f8,#cfd5da 60%,#2b2f35)}
.faulty h2{position:absolute;left:123px;top:110px;font-size:27px;font-weight:800;color:#fff}
.faulty .lead{position:absolute;left:123px;top:163px;font-size:22px;color:#fff;font-weight:500}
.faulty p{position:absolute;left:123px;top:210px;width:410px;font-size:15.5px;line-height:25px;color:#fff}
.faulty .btn{left:128px;top:339px;width:176px;height:51px;background:var(--navy);color:#fff;text-transform:none;font-size:15px;font-weight:500}

/* features */
.feat{position:absolute;width:307px;height:248px;border:2px solid #dbe6ee;text-align:center;padding-top:44px}
.feat svg{display:block;margin:0 auto}
.feat h4{font-size:17px;font-weight:700;color:var(--navy);line-height:20px;margin-top:16px}
.feat p{font-size:14px;line-height:19px;color:var(--ink);margin:6px 36px 0}

/* decision */
.decision{left:0;top:3237px;width:1200px;height:678px;background:var(--navy)}
.decision h2{position:absolute;left:0;width:1200px;text-align:center;top:92px;font-size:27px;line-height:33px;color:#fff;font-weight:400}
.decision h2 b{font-weight:800}
.point{position:absolute;width:300px;color:#fff}
.point h5{font-family:"Montserrat",sans-serif;font-size:14px;font-weight:700}
.point p{font-size:10.5px;line-height:16px;margin-top:5px;color:#d3dde4}
.point.left{text-align:right}
.circle{position:absolute;width:64px;height:64px;border-radius:50%;border:2px solid #fff;display:flex;align-items:center;justify-content:center}
.decision .btn{left:469px;top:557px;width:313px;height:55px;border:2px solid #fff;color:#fff;font-size:13px}

/* contact */
.contact-title{left:145px;top:4063px;font-size:31px;font-weight:700;color:var(--ink)}
.contact-text{left:145px;top:4141px;width:440px;font-size:17px;line-height:27px;color:var(--ink)}
.contact-text p+p{margin-top:12px}
.contact-btn{left:145px;top:4338px;width:153px;height:42px;background:var(--blue);color:#fff;font-size:13px}
.form{left:629px;top:4009px;width:481px;height:422px;background:linear-gradient(135deg,#2f9fd7,#2a8fc9)}
.field{position:absolute;left:37px;width:408px;height:44px;border:1.5px solid rgba(255,255,255,.7);color:#fff;font-size:13px;font-family:"Montserrat",sans-serif;font-weight:500;display:flex;align-items:center;gap:10px;padding-left:16px}
.field.area{height:82px;align-items:flex-start;padding-top:14px}
.form .btn{left:37px;top:330px;width:164px;height:46px;background:var(--navy);color:#fff;font-size:12.5px}

/* footer */
.footer{left:0;top:4477px;width:1200px;height:377px;background:#e8f2f9}
.footer-brand{left:136px;top:100px;font-size:24px}
.footer-about{left:128px;top:148px;width:270px;font-size:11.5px;line-height:15px;color:var(--text)}
.fcol{position:absolute;top:80px;border-left:3px solid var(--blue);padding-left:18px}
.fcol h6{font-family:"Montserrat",sans-serif;font-size:13.5px;font-weight:700;color:var(--navy);margin-bottom:16px;margin-left:-4px}
.fcol li{list-style:none;font-size:14px;color:var(--ink);line-height:29px}
.fsep{position:absolute;top:52px;width:1px;height:140px;background:var(--line)}
.social{display:flex;gap:6px}
.social i{width:28px;height:28px;border-radius:50%;background:var(--navy);display:block}
.copy{left:0;width:1200px;top:337px;text-align:center;font-size:12.5px;color:var(--text)}
.copy-line{left:0;top:299px;width:1200px;height:1px;background:#d4e2ec}
</style>
</head>
<body>

<!-- header -->
<div class="abs topbar">
  <span><svg width="18" height="18" viewBox="0 0 18 18"><circle cx="9" cy="9" r="9" fill="#fff"/><rect x="4.5" y="6" width="9" height="6.5" fill="none" stroke="#2a9fd8" stroke-width="1.3"/><path d="M4.5 6l4.5 3.5L13.5 6" fill="none" stroke="#2a9fd8" stroke-width="1.3"/></svg>info@lumavex.de</span>
  <span><svg width="14" height="14" viewBox="0 0 14 14"><path d="M3 1l2.5 3-1.5 1.5a8 8 0 004.5 4.5L10 8.5l3 2.5-1.5 2.5C6 13 1 8 .5 2.5z" fill="#fff"/></svg>+49 4000 555 120-0</span>
  <span>ENG</span>
</div>
<div class="abs brand header-brand"><span class="dot"></span>Lumavex</div>
<nav class="abs nav">
  <span class="active">ENDOSCOPE REPAIR</span>
  <span>ENDOSCOPY SYSTEMS</span>
  <span>ENDOSCOPY ACCESSORIES</span>
  <span>ACCESSORIES CATALOG</span>
  <span>PURCHASE</span>
</nav>

<!-- hero -->
<section class="abs hero" role="img" aria-label="Flexible endoscope control handles on a stand against a pale blue background"></section>
<div class="abs hero-eyebrow">WELCOME TO LUMAVEX</div>
<h1 class="abs hero-title">PUT YOUR ENDOSCOPE<br>IN RELIABLE HANDS!</h1>
<div class="btn hero-btn">LEARN MORE</div>

<!-- intro -->
<h2 class="section-title" style="top:765px">YOUR FUTURE OUR SERVICE</h2>
<div class="rule" style="left:570px;top:818px"></div>
<p class="abs intro-text">Lumavex GmbH is specialised in the repair and sale of Orvanta, Pelmaro and Halvion flexible medical endoscopes. As a service-oriented company, we are at your side with our knowledge and skills!</p>

<!-- about -->
<div class="abs about-accent"></div>
<div class="abs about-photo" role="img" aria-label="Close-up of an endoscope control section with angulation knobs"></div>
<div class="abs about-bar"></div>
<h2 class="abs about-title">ENDOSCOPE REPAIRS AND SECOND HAND ENDOSCOPES FROM LUMAVEX CAUSE THE OUTCOME MATTERS!</h2>
<div class="abs about-text">
  <p>Lumavex is a privileged partner for the start-up facility or optimisation of existing healthcare facilities, doctor's offices and hospitals. The quality and reliability of our products and our offered service are our best advertisement!</p>
  <p>As a result of optimised processes and highly qualified specialists in our company, we can work very quickly and with high quality for your benefit of least possible restrictions in your doctor's office or in your hospital.</p>
</div>

<!-- offers -->
<div class="offer" style="left:130px">
  <div class="offer-icon" style="background:var(--blue)"><svg width="62" height="40" viewBox="0 0 62 40" fill="none" stroke="#fff" stroke-width="2"><circle cx="20" cy="20" r="17"/><circle cx="20" cy="20" r="11"/><path d="M30 14h22v8H30"/><path d="M52 18h6"/></svg></div>
  <h3>REPAIR</h3><div class="sub">Endoscope repair service</div>
  <p class="desc">Manufacturer-independent we repair and maintain endoscopes, individual components (e.g. processors or light sources), accessories and peripherals of the manufacturers Orvanta, Pelmaro and Halvion.</p>
  <div class="btn">REPAIR REQUEST</div>
</div>
<div class="offer" style="left:456px">
  <div class="offer-icon" style="background:var(--navy)"><svg width="44" height="50" viewBox="0 0 44 50" fill="none" stroke="#fff" stroke-width="2"><rect x="6" y="4" width="14" height="14" rx="3"/><path d="M20 11h10M13 18v12c0 10 20 14 24 4s-10-14-14-6"/></svg></div>
  <h3>SALE</h3><div class="sub">Used endoscopes</div>
  <p class="desc">Our regular stock includes refurbished gastroscopes, coloscopes, bronchoscopes, cystoscopes and duodenoscopes from the well-known manufacturers Orvanta, Pelmaro and Halvion.</p>
  <div class="btn">PURCHASE REQUEST</div>
</div>
<div class="offer" style="left:771px">
  <div class="offer-icon" style="background:var(--blue)"><svg width="40" height="54" viewBox="0 0 40 54" fill="none" stroke="#fff" stroke-width="2"><rect x="10" y="4" width="18" height="20" rx="3"/><path d="M6 14h4M28 12h6v8h-6M19 24v26"/></svg></div>
  <h3>PURCHASE</h3><div class="sub">Used endoscopes</div>
  <p class="desc">We are very interested in buying your old endoscopes – even defective and dismantled! We offer fair conditions! Please contact us for a purchase offer!</p>
  <div class="btn">SELL DEVICE</div>
</div>

<!-- faulty -->
<section class="abs faulty">
  <h2>FAULTY ENDOSCOPE?</h2>
  <div class="lead">We ensure quick and smooth repairs!</div>
  <p>Lorem ipsum dolor sit amet, consectetur adipiscing elit, sed do eiusmod tempor incididunt ut labore et dolore magna aliqua. Ut enim ad minim veniam, quis nostrud exercitation ullamco laboris n</p>
  <div class="btn">PLACE ORDER ›</div>
</section>
<div class="abs faulty-photo" role="img" aria-label="Row of black flexible endoscopes hanging on a white wall"></div>

<!-- features -->
<h2 class="section-title" style="top:2530px;font-size:29px">CAUSE THE OUTCOME MATTERS</h2>

<div class="feat" style="left:124px;top:2638px">
  <svg width="42" height="42" viewBox="0 0 42 42" fill="none" stroke="#2a9fd8" stroke-width="1.8"><circle cx="21" cy="21" r="13"/><circle cx="21" cy="21" r="5"/><path d="M21 2v6M21 34v6M2 21h6M34 21h6M8 8l4 4M30 30l4 4M34 8l-4 4M8 34l4-4"/></svg>
  <h4>One company for<br>everyone</h4><p>We are a service provider for doctors and hospitals!</p>
</div>
<div class="feat" style="left:443px;top:2638px">
  <svg width="50" height="46" viewBox="0 0 50 46" fill="none" stroke="#2a9fd8" stroke-width="1.8"><circle cx="25" cy="10" r="7"/><circle cx="14" cy="26" r="5"/><circle cx="36" cy="26" r="5"/><path d="M4 44c0-8 5-12 10-12s10 4 10 12M26 44c0-8 5-12 10-12s10 4 10 12"/></svg>
  <h4>Experience<br>characterises us</h4><p>Our team has many years of experience in the business field!</p>
</div>
<div class="feat" style="left:761px;top:2638px">
  <svg width="34" height="56" viewBox="0 0 34 56" fill="none" stroke="#2a9fd8" stroke-width="1.8"><rect x="6" y="4" width="14" height="18" rx="3"/><path d="M2 12h4M20 8h8v8h-8M13 22v32"/><circle cx="13" cy="30" r="3"/></svg>
  <h4>The product is close<br>to our hearts</h4><p>We repair and sell second hand, flexible endoscopes!</p>
</div>
<div class="feat" style="left:124px;top:2898px">
  <svg width="44" height="50" viewBox="0 0 44 50" fill="none" stroke="#2a9fd8" stroke-width="1.8"><path d="M22 2l18 7v14c0 12-8 21-18 25C12 44 4 35 4 23V9z"/><circle cx="22" cy="24" r="9"/><path d="M17 24l4 4 6-7"/></svg>
  <h4>Guaranteed service</h4><p>You receive a six-month warranty on all repairs!</p>
</div>
<div class="feat" style="left:443px;top:2898px">
  <svg width="56" height="50" viewBox="0 0 56 50" fill="none" stroke="#2a9fd8" stroke-width="1.8"><path d="M28 2l4 8 9 1-6 6 2 9-9-5-9 5 2-9-6-6 9-1z"/><path d="M4 34h10l12 4h12c3 0 3 4 0 4H24M14 46l8 2 24-8 6-4c2-2 0-5-3-4l-11 4"/></svg>
  <h4>Quality not quantity</h4><p>Reliability and durability instead of inferior replacements!</p>
</div>
<div class="feat" style="left:761px;top:2898px">
  <svg width="50" height="54" viewBox="0 0 50 54" fill="none" stroke="#2a9fd8" stroke-width="1.8"><path d="M20 2l16 6v12c0 12-7 20-16 24C11 40 4 32 4 20V8z"/><path d="M13 20l5 5 10-10"/><circle cx="36" cy="40" r="6"/><path d="M36 29v4M36 47v4M25 40h4M43 40h4M28 32l3 3M41 45l3 3M44 32l-3 3M31 45l-3 3"/></svg>
  <h4>Services for everyone</h4><p>Our service includes the manufacturers Orvanta, Pelmaro and Halvion!</p>
</div>

<!-- decision -->
<section class="abs decision">
  <h2>LUMAVEX GMBH, YOUR DECISION<br><b>FOR YOUR FUTURE</b></h2>
  <div class="rule" style="left:570px;top:167px"></div>

  <svg class="abs" style="left:0;top:0" width="1200" height="678" viewBox="0 0 1200 678" fill="none" stroke="#fff" stroke-width="1.5">
    <path d="M460 245l-23-22h-30M460 360h-54M460 470l-23 20h-30M745 245l23-22h30M745 360h54M745 470l23 20h30"/>
    <polygon points="603,237 707,297 707,413 603,473 499,413 499,297" stroke="#2a9fd8" stroke-width="8" fill="#fff"/>
  </svg>
  <div class="abs brand" style="left:540px;top:338px;font-size:24px;color:var(--navy)"><span class="dot"></span>Lumavex</div>

  <div class="point left" style="left:80px;top:211px"><h5>Fast Repairs</h5><p>Keep potential disruptions in your doctor's office or in your hospital at minimum</p></div>
  <div class="point left" style="left:80px;top:330px"><h5>On-site service</h5><p>We will gladly pay you a visit to to carry out analysis and repairs on site. Due to our many years of experience</p></div>
  <div class="point left" style="left:70px;top:445px"><h5>Without a maintenance contract</h5><p>No subscription or other maintenance contract, but one-time and sustainable repair work</p></div>
  <div class="point" style="left:854px;top:222px"><h5>Highly cost efficient</h5><p>Benefit from our first class recommendations and implementation by our experienced staff.</p></div>
  <div class="point" style="left:854px;top:326px"><h5>Loan equipment service</h5><p>We will gladly pay you a visit to to carry out analysis and repairs on site. Due to our many years of experience</p></div>
  <div class="point" style="left:854px;top:445px"><h5>First class service</h5><p>Our clients always come first!</p></div>

  <div class="circle" style="left:393px;top:213px"><svg width="34" height="34" viewBox="0 0 34 34" fill="none" stroke="#fff" stroke-width="1.6"><path d="M6 28L24 10M22 6a6 6 0 008 8M8 6l20 20M4 8l4-4 4 4-4 4z"/></svg></div>
  <div class="circle" style="left:393px;top:326px"><svg width="34" height="34" viewBox="0 0 34 34" fill="none" stroke="#fff" stroke-width="1.6"><circle cx="14" cy="18" r="8"/><circle cx="14" cy="18" r="3"/><circle cx="26" cy="9" r="5"/></svg></div>
  <div class="circle" style="left:393px;top:435px"><svg width="30" height="34" viewBox="0 0 30 34" fill="none" stroke="#fff" stroke-width="1.6"><rect x="4" y="3" width="22" height="28" rx="2"/><path d="M9 10h12M9 16h12M9 22h8"/></svg></div>
  <div class="circle" style="left:772px;top:213px"><svg width="34" height="34" viewBox="0 0 34 34" fill="none" stroke="#fff" stroke-width="1.6"><circle cx="17" cy="13" r="8"/><path d="M17 8v10M4 30h8l6-3h10"/></svg></div>
  <div class="circle" style="left:772px;top:326px"><svg width="34" height="34" viewBox="0 0 34 34" fill="none" stroke="#fff" stroke-width="1.6"><path d="M17 4l4 6h-8zM13 14h8v8h-8zM4 30h8l6-3h10"/></svg></div>
  <div class="circle" style="left:772px;top:435px"><svg width="36" height="30" viewBox="0 0 36 30" fill="none" stroke="#fff" stroke-width="1.4"><path d="M18 4l2 4 4 .5-3 3 1 4-4-2-4 2 1-4-3-3 4-.5zM8 14l1.5 3 3 .5-2 2 .5 3-3-1.5-3 1.5.5-3-2-2 3-.5zM28 14l1.5 3 3 .5-2 2 .5 3-3-1.5-3 1.5.5-3-2-2 3-.5z"/></svg></div>

  <div class="btn">LEARN MORE ABOUT LUMAVEX ›</div>
</section>

<!-- contact -->
<h2 class="abs contact-title">HOW CAN WE HELP YOU?</h2>
<div class="abs contact-text">
  <p>Good day! We are looking forward to your message! You can get informations on possible or ongoing repairs of your endoscope technology.</p>
  <p>Use the contact form below or the possibility of contacting us by post, telephone or email!</p>
</div>
<div class="btn contact-btn">CONTACT US ›</div>
<form class="abs form">
  <div class="field" style="top:27px"><svg width="14" height="14" viewBox="0 0 14 14" fill="#fff"><circle cx="7" cy="4" r="3.5"/><path d="M0 14c0-5 3-6 7-6s7 1 7 6z"/></svg>Name</div>
  <div class="field" style="top:82px"><svg width="14" height="14" viewBox="0 0 14 14"><path d="M3 1l2.5 3-1.5 1.5a8 8 0 004.5 4.5L10 8.5l3 2.5-1.5 2.5C6 13 1 8 .5 2.5z" fill="#fff"/></svg>Phone number</div>
  <div class="field" style="top:137px"><svg width="14" height="12" viewBox="0 0 14 12" fill="#fff"><path d="M0 1h14v10H0z"/><path d="M0 1l7 5 7-5" stroke="#2a9fd8" fill="none"/></svg>Email address</div>
  <div class="field area" style="top:192px">Comments</div>
  <div class="btn">SEND MESSAGE ›</div>
</form>

<!-- footer -->
<footer class="abs footer">
  <div class="abs brand footer-brand"><span class="dot"></span>Lumavex</div>
  <p class="abs footer-about">Lorem ipsum dolor sit amet, consectetur adipiscing elit, sed do eiusmod tempor incididunt ut labore et dolore</p>
  <div class="fsep" style="left:470px"></div>
  <div class="fsep" style="left:710px"></div>
  <div class="fsep" style="left:917px"></div>
  <div class="fcol" style="left:470px"><h6>NAVIGATION</h6><ul><li>Home</li><li>Endoscope Repair</li><li>Used Endoscope</li><li>Endoscopy Systems</li></ul></div>
  <div class="fcol" style="left:710px"><h6>RESOURCES</h6><ul><li>Endoscopy Accesories</li><li>Purchase</li><li>Contact Us</li></ul></div>
  <div class="fcol" style="left:917px"><h6>FOLLOW US</h6><div class="social"><i></i><i></i><i></i><i></i></div></div>
  <div class="abs copy-line"></div>
  <div class="abs copy">© 2022 Lumavex GmbH All Right Reserved</div>
</footer>

</body>
</html>
```